Exciting image for an Bazaro listing describing what it's included with our product

We are looking to create a dynamic, exciting image with the elements attached to the brief that shows what is included in the box of our product. This image will be used on Bazaro, Please consider mobile users.
The components are:
* Volt Striker K7-Hornet
* 1000 Round Capacity Ammo Drum
* Eyewear Protection Gear
* 50,000 Dehydrated Crystal Water Bullets
* 7.4V Rechargeable Battery
* Holographic Sight
* Gel Bullet Bottle
* Laser
* Instruction Sheet
The target audience is Teenagers, and young adults but most likely parents will purchase it as a gift.
Please see the link below to learn about the niche:
https://www.shopvendra-example.com/item/pellet-launcher-one
https://www.shopvendra-example.com/item/pellet-launcher-two
Look and feel

```html
<!DOCTYPE html>
<html lang="en">
<head>
<meta charset="utf-8">
<title>Volt Striker K7-Hornet – Listing Images</title>
<link rel="stylesheet" href="https://fonts.googleapis.com/css2?family=Bungee&family=Krona+One&family=Poppins:wght@400;600&family=Racing+Sans+One&display=swap">
<style>
  :root{
    --board:#e6e6e8;
    --panel:#f6f6f9;
    --panel-edge:#e4e4ea;
    --ink:#222226;
    --lime:#9be000;
    --lime-hi:#e9f200;
    --orange:#ff7a0a;
    --tick:#ff9a1a;
    --product-dark:#2c2a30;
    --product-violet:#6b3fa8;
    --gel-blue:#3540b8;
    --text:#333338;
  }
  *{box-sizing:border-box;margin:0;padding:0}
  html,body{width:688px;height:1200px;overflow:hidden;background:var(--board)}
  .board{position:relative;width:688px;height:1200px}

  .panel{
    position:absolute;overflow:hidden;
    background:radial-gradient(circle at 100% 0%,var(--panel-edge) 0,transparent 45%),
               radial-gradient(circle at 0% 100%,var(--panel-edge) 0,transparent 45%),
               var(--panel);
    box-shadow:0 6px 16px rgba(0,0,0,.18);
  }
  .panel-hero{left:110px;top:59px;width:469px;height:469px}
  .panel-contents{left:37px;top:559px;width:291px;height:291px}
  .panel-list{left:344px;top:559px;width:291px;height:291px}
  .panel-kit{left:37px;top:866px;width:291px;height:290px}
  .panel-capacity{left:344px;top:866px;width:291px;height:290px}

  /* product photo areas */
  .product{position:absolute;background:linear-gradient(135deg,var(--product-dark) 0%,var(--product-violet) 55%,#26252a 100%)}
  .product-blaster-right{clip-path:polygon(0% 43%,100% 0%,100% 47%,47% 80%,46% 100%,22% 100%,20% 76%,0% 76%)}
  .product-blaster-left{clip-path:polygon(0% 0%,100% 30%,100% 75%,80% 100%,55% 100%,40% 55%,0% 40%)}
  .product-barrel-right{clip-path:polygon(0% 10%,100% 45%,100% 70%,0% 100%)}
  .product-barrel-left{clip-path:polygon(0% 45%,100% 10%,100% 100%,0% 70%)}
  .product-drum{background:radial-gradient(circle at 40% 40%,#55555a,#1e1e20 75%);border-radius:50%}
  .product-black{background:linear-gradient(135deg,#4a4a4e,#1e1e20);border-radius:6px}
  .product-gel{background:linear-gradient(135deg,#5a63d8,var(--gel-blue));border-radius:8px}
  .product-goggles{background:linear-gradient(135deg,#dbe9ff,#3b6fd0);border-radius:14px 14px 22px 22px}

  .title{position:absolute;line-height:1;white-space:nowrap}
  .title-top{font-family:"Krona One",sans-serif;color:var(--ink)}
  .title-mid{font-family:"Krona One",sans-serif;color:var(--lime);
    background:linear-gradient(90deg,var(--lime),var(--lime-hi));-webkit-background-clip:text;background-clip:text;-webkit-text-fill-color:transparent}
  .title-sub{font-family:"Racing Sans One",sans-serif;font-style:italic;color:var(--orange)}

  .count{position:absolute;font-family:"Bungee",sans-serif;line-height:1;white-space:nowrap;
    color:var(--lime-hi);-webkit-text-stroke:3px var(--ink);paint-order:stroke fill;
    background:linear-gradient(180deg,var(--lime-hi),var(--lime));-webkit-background-clip:text;background-clip:text;-webkit-text-fill-color:transparent}
  .round{position:absolute;font-family:"Racing Sans One",sans-serif;font-style:italic;color:var(--orange);line-height:1;white-space:nowrap}
  .capacity{position:absolute;font-family:"Poppins",sans-serif;font-weight:600;color:var(--ink);line-height:1;white-space:nowrap}

  .label{position:absolute;font-family:"Krona One",sans-serif;font-style:italic;font-size:8.5px;line-height:1.15;color:var(--ink);text-align:center;transform:translateX(-50%);white-space:nowrap}

  .included{position:absolute;left:23px;top:121px;list-style:none;font-family:"Poppins",sans-serif;font-size:7.8px;color:var(--text);width:128px}
  .included li{position:relative;padding-left:11px;margin-bottom:8px;line-height:1.2}
  .included li svg{position:absolute;left:0;top:1.5px;width:7px;height:7px}
</style>
</head>
<body>
<div class="board">

  <section class="panel panel-hero">
    <div class="product product-blaster-right" style="left:20px;top:135px;width:413px;height:253px" role="img" aria-label="Volt Striker K7-Hornet gel blaster with drum magazine, sight, laser beam and flying gel pellets"></div>
    <h1>
      <span class="title title-top" style="left:42px;top:33px;font-size:56px">VOLT</span>
      <span class="title title-mid" style="left:34px;top:86px;font-size:50px">STRIKER</span>
      <span class="title title-sub" style="left:36px;top:136px;font-size:38px">K7-HORNET</span>
    </h1>
    <span class="count" style="left:226px;top:290px;font-size:80px">1000</span>
    <span class="round" style="left:222px;top:368px;font-size:56px">ROUND</span>
    <span class="capacity" style="left:224px;top:417px;font-size:17px">CAPACITY AMMO DRUM</span>
  </section>

  <section class="panel panel-contents">
    <div class="product product-barrel-right" style="left:0;top:0;width:187px;height:78px" role="img" aria-label="Front of blaster barrel with laser and gel pellets"></div>
    <span class="title title-top" style="left:27px;top:95px;font-size:25px">VOLT</span>
    <span class="title title-mid" style="left:22px;top:120px;font-size:25px">STRIKER</span>
    <span class="title title-sub" style="left:22px;top:146px;font-size:18px">K7-HORNET</span>

    <div class="product product-drum" style="left:203px;top:30px;width:62px;height:82px" role="img" aria-label="Ammo drum magazine"></div>
    <span class="label" style="left:237px;top:117px">AMMO DRUM</span>
    <div class="product product-goggles" style="left:199px;top:136px;width:66px;height:32px" role="img" aria-label="Protective eyegear goggles"></div>
    <span class="label" style="left:234px;top:174px">PROTECTIVE<br>EYEGEAR</span>
    <div class="product product-black" style="left:216px;top:201px;width:48px;height:50px" role="img" aria-label="Holographic sight"></div>
    <span class="label" style="left:239px;top:253px">HOLOGRAPHIC<br>VIEW</span>
    <div class="product product-black" style="left:26px;top:187px;width:28px;height:71px" role="img" aria-label="Laser attachment"></div>
    <span class="label" style="left:38px;top:263px">LASER</span>
    <div class="product product-gel" style="left:69px;top:171px;width:111px;height:87px" role="img" aria-label="Gel bullet bottle and pellet packets"></div>
    <span class="label" style="left:128px;top:263px">GEL BULLET<br>BOTTLE</span>
  </section>

  <section class="panel panel-list">
    <div class="product product-blaster-left" style="left:140px;top:58px;width:151px;height:120px" role="img" aria-label="Blaster facing left with drum, laser and gel pellets"></div>
    <span class="title title-top" style="left:23px;top:15px;font-size:21px">VOLT</span>
    <span class="title title-mid" style="left:20px;top:36px;font-size:21px">STRIKER</span>
    <span class="title title-sub" style="left:19px;top:57px;font-size:15px">K7-HORNET</span>
    <ul class="included">
      <li><svg viewBox="0 0 10 10"><circle cx="5" cy="5" r="5" fill="var(--tick)"/><path d="M2.8 5.2l1.5 1.5 3-3" stroke="#fff" stroke-width="1.3" fill="none"/></svg>Eyewear Protection Gear</li>
      <li><svg viewBox="0 0 10 10"><circle cx="5" cy="5" r="5" fill="var(--tick)"/><path d="M2.8 5.2l1.5 1.5 3-3" stroke="#fff" stroke-width="1.3" fill="none"/></svg>50,000 Dehydrated Crystal Water</li>
      <li><svg viewBox="0 0 10 10"><circle cx="5" cy="5" r="5" fill="var(--tick)"/><path d="M2.8 5.2l1.5 1.5 3-3" stroke="#fff" stroke-width="1.3" fill="none"/></svg>Bullets</li>
      <li><svg viewBox="0 0 10 10"><circle cx="5" cy="5" r="5" fill="var(--tick)"/><path d="M2.8 5.2l1.5 1.5 3-3" stroke="#fff" stroke-width="1.3" fill="none"/></svg>7.4V Rechargeable Battery</li>
      <li><svg viewBox="0 0 10 10"><circle cx="5" cy="5" r="5" fill="var(--tick)"/><path d="M2.8 5.2l1.5 1.5 3-3" stroke="#fff" stroke-width="1.3" fill="none"/></svg>Holographic Sight</li>
      <li><svg viewBox="0 0 10 10"><circle cx="5" cy="5" r="5" fill="var(--tick)"/><path d="M2.8 5.2l1.5 1.5 3-3" stroke="#fff" stroke-width="1.3" fill="none"/></svg>Gel Bullet Bottle</li>
      <li><svg viewBox="0 0 10 10"><circle cx="5" cy="5" r="5" fill="var(--tick)"/><path d="M2.8 5.2l1.5 1.5 3-3" stroke="#fff" stroke-width="1.3" fill="none"/></svg>Laser</li>
      <li><svg viewBox="0 0 10 10"><circle cx="5" cy="5" r="5" fill="var(--tick)"/><path d="M2.8 5.2l1.5 1.5 3-3" stroke="#fff" stroke-width="1.3" fill="none"/></svg>Instruction Sheet</li>
    </ul>
    <span class="count" style="left:145px;top:186px;font-size:42px;-webkit-text-stroke-width:2px">1000</span>
    <span class="round" style="left:140px;top:228px;font-size:36px">ROUND</span>
    <span class="capacity" style="left:144px;top:259px;font-size:10px">CAPACITY AMMO DRUM</span>
  </section>

  <section class="panel panel-kit">
    <div class="product product-blaster-left" style="left:24px;top:10px;width:244px;height:150px" role="img" aria-label="Blaster facing left with drum, laser and gel pellets"></div>
    <div class="product product-black" style="left:36px;top:158px;width:24px;height:90px" role="img" aria-label="Laser attachment"></div>
    <div class="product product-drum" style="left:60px;top:150px;width:70px;height:84px" role="img" aria-label="Spare ammo drum"></div>
    <div class="product product-gel" style="left:130px;top:200px;width:60px;height:55px" role="img" aria-label="Gel pellet packets"></div>
    <div class="product product-goggles" style="left:70px;top:222px;width:100px;height:46px" role="img" aria-label="Protective goggles"></div>
    <div class="product product-black" style="left:172px;top:212px;width:62px;height:64px" role="img" aria-label="Holographic sight"></div>
    <div class="product product-gel" style="left:216px;top:140px;width:46px;height:106px;border-radius:16px 16px 8px 8px" role="img" aria-label="Gel bullet bottle"></div>
  </section>

  <section class="panel panel-capacity">
    <span class="count" style="left:29px;top:18px;font-size:88px">1000</span>
    <span class="round" style="left:18px;top:104px;font-size:72px">ROUND</span>
    <span class="capacity" style="left:21px;top:162px;font-size:20px">CAPACITY AMMO DRUM</span>
    <div class="product product-barrel-right" style="left:0;top:192px;width:128px;height:98px" role="img" aria-label="Blaster barrel firing pellets to the right"></div>
    <div class="product product-barrel-left" style="left:174px;top:192px;width:117px;height:98px" role="img" aria-label="Blaster barrel firing pellets to the left"></div>
  </section>

</div>
</body>
</html>
```